I want a website to be designed for our new company, it's an import and export company for variety of things.

please see the attached Logo for our company and the Images for our different sections for our busienss

Target Market(s)

multiple

Coding

Coded - Design and coding required

Number of Pages Required

5+ page

Font styles to use
Sans Serif

Colors

Designer to choose colors to be used in the design.

Requirements
Must have
• KVR GLOBALINKS
• KVR globalinks Trading & Contracting provides various services. The Company offers infrastructure construction, oil, enegy and gas services, agricultural projects, real estate development, travel and tourism, and food processing and trading.
• Civil contracting for infrastructure, residential and heavy projects. Through its main subsidiaries; distribution of general food products, construction chemicals including corrosion inhibitors and electrical machinery; provides catering and travel agency services; ownership and operation of a school; offers human sources services including manpower supply.
• Drilling and Gold Mines Used Machinery, All Kinds of Construction Machinery, Drilling Machines are manufactured and sold.
Nice to have
• good designa and beautiful colours, it has too look professional

```html
<!DOCTYPE html>
<html lang="en">
<head>
<meta charset="utf-8">
<title>KVR GLOBALINKS</title>
<link rel="stylesheet" href="https://fonts.googleapis.com/css2?family=Cinzel:wght@400;700&family=Lato:wght@400;700&family=Roboto:wght@400;500;700&display=swap">
<style>
:root{
  --black:#000;
  --card:#1b1b1d;
  --footer:#1e1e20;
  --red:#e31d2b;
  --red-deep:#b5121f;
  --white:#fff;
  --dim:#8d8d8f;
}
*{box-sizing:border-box;margin:0;padding:0}
html,body{width:1200px;height:3658px;overflow:hidden;background:var(--black)}
body{position:relative;font-family:"Lato",sans-serif;color:var(--white)}
.abs{position:absolute}
.serif{font-family:"Cinzel",serif;font-weight:400}

/* hero */
.hero{left:0;top:0;width:1200px;height:770px}
.hero-photo{left:0;top:0;width:1200px;height:770px}
.nav{top:80px;font-family:"Roboto",sans-serif;font-weight:500;font-size:13px;letter-spacing:.3px}
.nav a{position:absolute;color:var(--white);text-decoration:none;white-space:nowrap}
.nav a.active::after{content:"";position:absolute;left:0;right:0;top:21px;height:2px;background:var(--red)}
.brand{left:480px;top:78px;width:240px;text-align:center;font-family:"Cinzel",serif;font-size:20px;letter-spacing:2px;color:var(--white)}
.phone{left:902px;top:32px;font-family:"Roboto",sans-serif;font-weight:500;font-size:18px;display:flex;align-items:center;gap:6px}
.welcome{left:0;width:1200px;top:300px;text-align:center;font-size:36px;letter-spacing:1px}
.hero-title{left:0;width:1200px;top:350px;text-align:center;font-size:53px;font-weight:700;letter-spacing:1px}
.btn-red{background:var(--red);color:var(--white);font-family:"Roboto",sans-serif;font-weight:500;font-size:17px;display:flex;align-items:center;justify-content:center}
.hero-btn{left:514px;top:432px;width:184px;height:50px}
.arrow{width:52px;height:52px;border-radius:50%;background:rgba(255,255,255,.75);display:flex;align-items:center;justify-content:center}

/* who we are */
.sec-title{left:0;width:1200px;text-align:center;font-size:32px;letter-spacing:.5px}
.rule{height:2px;width:64px;left:568px}
.who-text{left:200px;width:820px;top:914px;text-align:center;font-size:16px;line-height:31px;color:#e6e6e6}
.btn-outline{border:2px solid var(--white);color:var(--white);font-family:"Roboto",sans-serif;font-weight:500;font-size:16px;display:flex;align-items:center;justify-content:center}

/* services */
.service{top:1230px;width:600px;height:453px}
.service-title{left:0;width:600px;top:178px;text-align:center;font-size:30px;font-weight:700}
.service-text{left:138px;width:370px;top:228px;text-align:center;font-size:14.5px;line-height:21px;color:#f2f2f2}
.service-toggle{left:303px;top:333px;width:42px;height:42px;border-radius:50%;border:2px solid var(--white);display:flex;align-items:center;justify-content:center}

/* projects */
.project{top:1818px;width:301px;height:357px;background:var(--card)}
.project-photo{left:0;top:0;width:301px;height:170px}
.project-title{left:27px;top:194px;width:250px;font-family:"Roboto",sans-serif;font-weight:500;font-size:18px;line-height:23px}
.project-text{left:27px;top:248px;width:250px;font-size:11px;line-height:17px;color:#e0e0e0}
.project-link{left:27px;top:316px;font-family:"Roboto",sans-serif;font-weight:700;font-size:11.5px;color:var(--red)}

/* machines */
.machines{left:0;top:2218px;width:1200px;height:502px}
.machines-title{left:140px;top:2310px;font-size:29px;line-height:36px;letter-spacing:.5px}
.machines-text{left:141px;top:2410px;width:350px;font-size:14px;line-height:27.5px}

/* contact */
.contact{left:0;top:2720px;width:1200px;height:575px}
.field{background:rgba(0,0,0,.82);border:1px solid #5a5a5a;color:#e6e6e6;font-size:14px;padding:0 20px;display:flex;align-items:center}
.field.tall{align-items:flex-start;padding-top:20px}

/* footer */
.footer{left:0;top:3295px;width:1200px;height:363px;background:var(--footer)}
.foot-head{top:3320px;font-family:"Roboto",sans-serif;font-weight:400;font-size:18px;letter-spacing:.3px}
.foot-list{top:3368px;list-style:none;font-size:16px;color:var(--dim);line-height:28.5px}
.foot-list li::before{content:"» ";color:var(--dim)}
.contact-line{font-size:16px;color:var(--dim);display:flex;gap:14px;align-items:flex-start;line-height:18px}
.social{list-style:none;font-size:16px;color:var(--dim)}
.social li{display:flex;align-items:center;gap:18px;height:36px}
.social .dot{width:12px;height:12px;border-radius:50%;background:#e6e6e6}
.copy{left:0;width:1200px;top:3612px;text-align:center;font-size:14px;color:#bbb}
</style>
</head>
<body>

<!-- Hero -->
<section class="abs hero">
  <svg class="abs hero-photo" width="1200" height="770" role="img" aria-label="Offshore oil rig at sea under a dramatic sunset sky">
    <defs>
      <linearGradient id="sky" x1="0" y1="0" x2="0" y2="1">
        <stop offset="0" stop-color="#232b3c"/>
        <stop offset=".3" stop-color="#4a5872"/>
        <stop offset=".5" stop-color="#7d5c6c"/>
        <stop offset=".6" stop-color="#a66a55"/>
        <stop offset=".7" stop-color="#3b4a60"/>
        <stop offset="1" stop-color="#1b2433"/>
      </linearGradient>
    </defs>
    <path d="M0 0H1200V700L600 765L0 700Z" fill="url(#sky)"/>
    <path d="M0 700L600 765L1200 700" fill="none" stroke="#4b4f58" stroke-width="3"/>
  </svg>

  <nav class="abs nav" style="left:0;width:1200px">
    <a class="active" style="left:106px">HOME</a>
    <a style="left:177px">ABOUT US</a>
    <a style="left:274px">SERVICES</a>
    <a style="left:369px">PROJECTS</a>
    <a style="left:763px">NEWS</a>
    <a style="left:833px">TESTIMONIALS</a>
    <a style="left:962px">CONTACT US</a>
  </nav>
  <div class="abs brand">KVR GLOBALINKS</div>
  <div class="abs phone">
    <svg width="18" height="18" viewBox="0 0 24 24"><path d="M6.6 10.8a15 15 0 0 0 6.6 6.6l2.2-2.2c.3-.3.7-.4 1-.2 1.1.4 2.3.6 3.6.6.6 0 1 .4 1 1V20c0 .6-.4 1-1 1A17 17 0 0 1 3 4c0-.6.4-1 1-1h3.5c.6 0 1 .4 1 1 0 1.3.2 2.5.6 3.6.1.3 0 .7-.2 1z" fill="#e31d2b"/></svg>
    (555) 010 2040
  </div>

  <div class="abs arrow" style="left:104px;top:362px"><svg width="18" height="18" viewBox="0 0 20 20"><path d="M13 3L6 10l7 7" fill="none" stroke="#222" stroke-width="2.4"/></svg></div>
  <div class="abs arrow" style="left:1037px;top:362px"><svg width="18" height="18" viewBox="0 0 20 20"><path d="M7 3l7 7-7 7" fill="none" stroke="#222" stroke-width="2.4"/></svg></div>

  <div class="abs welcome serif">WELCOME TO</div>
  <h1 class="abs hero-title serif">KVR GLOBALINKS</h1>
  <div class="abs btn-red hero-btn">LEARN MORE</div>
</section>

<!-- Who we are -->
<h2 class="abs sec-title serif" style="top:836px">WHO WE ARE</h2>
<div class="abs rule" style="top:887px;background:#d0d0d0"></div>
<p class="abs who-text">Etiam eleifend metus vitae adipiscing semper mauris ipsum iaculis elit congue gravida elit mi egestas orci Curabitur pede Maecenas aliquet velit vel turpis Mauris neque metus malesuada<br>Aec ultricies sit amet porttitor mattis enim In massa libero interdum nec interdum vel blandit sed nulla In ullamcorper est eget tempor cursus neque mi consectetuer mi a ultricies massa est sed nisl Class aptent taciti sociosqu ad litora torquent per conubia nostra per inceptos hymenaeos</p>
<div class="abs btn-outline" style="left:516px;top:1103px;width:188px;height:53px">LEARN MORE</div>

<!-- Services -->
<section class="abs service" style="left:0">
  <svg class="abs" width="600" height="453" role="img" aria-label="Container port with stacked shipping containers at sunset">
    <defs><linearGradient id="port" x1="0" y1="0" x2="0" y2="1"><stop offset="0" stop-color="#4a4a4c"/><stop offset=".25" stop-color="#8a6a44"/><stop offset=".5" stop-color="#4b4e55"/><stop offset="1" stop-color="#3a3840"/></linearGradient></defs>
    <rect width="600" height="453" fill="url(#port)"/>
  </svg>
  <h3 class="abs service-title serif" style="left:24px">TRADING</h3>
  <p class="abs service-text" style="left:140px">Aa libero interdum nec interdum vel blandit sed nulla In ullamcorper est eget tempor cursus neque mi consectetuer mi a ultricies massa est sed nisl Class aptent taciti sociosqu ad litora</p>
  <div class="abs service-toggle" style="left:303px"><svg width="16" height="16" viewBox="0 0 20 20"><path d="M4 7l6 6 6-6" fill="none" stroke="#fff" stroke-width="2.4"/></svg></div>
</section>
<section class="abs service" style="left:600px">
  <svg class="abs" width="600" height="453" role="img" aria-label="Construction workers pouring concrete on a site, red tinted">
    <defs><linearGradient id="build" x1="0" y1="0" x2="1" y2="1"><stop offset="0" stop-color="#e8414c"/><stop offset=".6" stop-color="#d63340"/><stop offset="1" stop-color="#b8242f"/></linearGradient></defs>
    <rect width="600" height="453" fill="url(#build)"/>
  </svg>
  <h3 class="abs service-title serif" style="left:-4px">CONTRACTING</h3>
  <p class="abs service-text" style="left:110px">Aa libero interdum nec interdum vel blandit sed nulla In ullamcorper est eget tempor cursus neque mi consectetuer mi a ultricies massa est sed nisl Class aptent taciti sociosqu ad litora</p>
  <div class="abs service-toggle" style="left:274px"><svg width="16" height="16" viewBox="0 0 20 20"><path d="M4 7l6 6 6-6" fill="none" stroke="#fff" stroke-width="2.4"/></svg></div>
</section>

<!-- Projects -->
<h2 class="abs sec-title serif" style="top:1732px">OUR PROJECTS</h2>
<div class="abs rule" style="top:1780px;background:#d0d0d0"></div>

<article class="abs project" style="left:127px">
  <svg class="abs project-photo" width="301" height="170" role="img" aria-label="Yellow drilling rig in a snowy forest"><defs><linearGradient id="p1" x1="0" y1="0" x2="0" y2="1"><stop offset="0" stop-color="#aebfc9"/><stop offset=".55" stop-color="#4d5a4e"/><stop offset="1" stop-color="#c9d2d8"/></linearGradient></defs><rect width="301" height="170" fill="url(#p1)"/></svg>
  <h4 class="abs project-title">Pellentesque faucibus Ut accumsan ultric</h4>
  <p class="abs project-text">Duis quam Nam eget lacus Aliquam erat volutpat Quisque dignissim congue leoMauris vel lacus vitae felis vestibulum</p>
  <a class="abs project-link">READ MORE</a>
</article>
<article class="abs project" style="left:452px">
  <svg class="abs project-photo" width="301" height="170" role="img" aria-label="Aerial view of a large building complex"><defs><linearGradient id="p2" x1="0" y1="0" x2="0" y2="1"><stop offset="0" stop-color="#7d8580"/><stop offset=".5" stop-color="#b9bdbd"/><stop offset="1" stop-color="#6f7670"/></linearGradient></defs><rect width="301" height="170" fill="url(#p2)"/></svg>
  <h4 class="abs project-title">Pellentesque faucibus Ut accumsan ultric</h4>
  <p class="abs project-text">Duis quam Nam eget lacus Aliquam erat volutpat Quisque dignissim congue leoMauris vel lacus vitae felis vestibulum</p>
  <a class="abs project-link">READ MORE</a>
</article>
<article class="abs project" style="left:776px">
  <svg class="abs project-photo" width="301" height="170" role="img" aria-label="Offshore drilling platform from above at sea"><defs><linearGradient id="p3" x1="0" y1="0" x2="0" y2="1"><stop offset="0" stop-color="#3b4a52"/><stop offset="1" stop-color="#1f2e36"/></linearGradient></defs><rect width="301" height="170" fill="url(#p3)"/></svg>
  <h4 class="abs project-title">Pellentesque faucibus Ut accumsan ultric</h4>
  <p class="abs project-text">Duis quam Nam eget lacus Aliquam erat volutpat Quisque dignissim congue leoMauris vel lacus vitae felis vestibulum</p>
  <a class="abs project-link">READ MORE</a>
</article>

<!-- Machines -->
<section class="abs machines">
  <svg class="abs" width="1200" height="502" role="img" aria-label="Yellow piling and drilling machines on a construction site under a cloudy sky">
    <defs>
      <linearGradient id="rig" x1="0" y1="0" x2="0" y2="1"><stop offset="0" stop-color="#5f86b4"/><stop offset=".4" stop-color="#b8c6d4"/><stop offset=".7" stop-color="#9a8a5a"/><stop offset="1" stop-color="#8a7d6c"/></linearGradient>
      <linearGradient id="wine" x1="0" y1="0" x2="1" y2="1"><stop offset="0" stop-color="#2a1416"/><stop offset=".55" stop-color="#7d0f19"/><stop offset="1" stop-color="#a01420"/></linearGradient>
    </defs>
    <rect width="1200" height="502" fill="url(#rig)"/>
    <path d="M0 0H685L438 502H0Z" fill="url(#wine)"/>
  </svg>
</section>
<h2 class="abs machines-title serif">MANUFACTURING &amp; SOLD<br>DRILLING MACHINES</h2>
<div class="abs" style="left:141px;top:2392px;width:64px;height:2px;background:#e6e6e6"></div>
<p class="abs machines-text">Nunc tempus felis vitae urna Vivamus porttitor neque at volutpat rutrum purus nisi eleifend<br>Aibero a tempus libero lectus feugiat felis Morbi diam mauris viverra in gravida eu mattis in ante Morbi eget arcu Morbi porta libero id ullamcorper</p>
<div class="abs btn-outline" style="left:147px;top:2582px;width:163px;height:45px;font-size:14px">LEARN MORE</div>

<!-- Contact -->
<section class="abs contact">
  <svg class="abs" width="1200" height="575" role="img" aria-label="Dark industrial machinery silhouette background">
    <defs><linearGradient id="dark" x1="0" y1="0" x2="0" y2="1"><stop offset="0" stop-color="#2a2a2c"/><stop offset=".5" stop-color="#3a3a3c"/><stop offset="1" stop-color="#1f1f21"/></linearGradient></defs>
    <rect width="1200" height="575" fill="url(#dark)"/>
  </svg>
</section>
<h2 class="abs sec-title serif" style="top:2794px">CONTACT US</h2>
<div class="abs rule" style="top:2840px;background:var(--red)"></div>
<div class="abs field" style="left:177px;top:2868px;width:409px;height:50px">Your Name</div>
<div class="abs field" style="left:598px;top:2868px;width:408px;height:50px">Phone</div>
<div class="abs field" style="left:177px;top:2930px;width:410px;height:50px">Email</div>
<div class="abs field" style="left:598px;top:2930px;width:410px;height:50px">City</div>
<div class="abs field tall" style="left:177px;top:2992px;width:827px;height:86px">Message</div>
<div class="abs btn-red" style="left:510px;top:3105px;width:196px;height:53px;font-weight:700;font-size:19px;background:var(--red-deep)">SUBMIT</div>

<!-- Footer -->
<footer class="abs footer"></footer>
<h5 class="abs foot-head" style="left:183px">QUICK LINKS</h5>
<ul class="abs foot-list" style="left:185px"><li>Home</li><li>About us</li><li>Who We Serve</li><li>Projects</li><li>Services</li></ul>
<h5 class="abs foot-head" style="left:384px">RESOURCES</h5>
<ul class="abs foot-list" style="left:385px"><li>News</li><li>Testimonials</li><li>Term of Use</li><li>Sitemap</li><li>Contact Us</li></ul>
<h5 class="abs foot-head" style="left:583px">CONTACT US</h5>
<div class="abs contact-line" style="left:588px;top:3368px">
  <svg width="16" height="20" viewBox="0 0 16 20"><path d="M8 1a6 6 0 0 0-6 6c0 4.5 6 12 6 12s6-7.5 6-12a6 6 0 0 0-6-6z" fill="none" stroke="#bbb" stroke-width="1.6"/><circle cx="8" cy="7" r="2" fill="none" stroke="#bbb" stroke-width="1.6"/></svg>
  <span>48 Harbor Lane Suite 2<br>Portside 20410 PS</span>
</div>
<div class="abs contact-line" style="left:588px;top:3422px">
  <svg width="18" height="18" viewBox="0 0 24 24"><path d="M6.6 10.8a15 15 0 0 0 6.6 6.6l2.2-2.2c.3-.3.7-.4 1-.2 1.1.4 2.3.6 3.6.6.6 0 1 .4 1 1V20c0 .6-.4 1-1 1A17 17 0 0 1 3 4c0-.6.4-1 1-1h3.5c.6 0 1 .4 1 1 0 1.3.2 2.5.6 3.6.1.3 0 .7-.2 1z" fill="none" stroke="#bbb" stroke-width="1.6"/></svg>
  <span>+1 (555) 014-2288</span>
</div>
<div class="abs contact-line" style="left:588px;top:3460px">
  <svg width="18" height="16" viewBox="0 0 18 14"><rect x="1" y="1" width="16" height="12" fill="none" stroke="#bbb" stroke-width="1.5"/><path d="M1 1l8 6 8-6" fill="none" stroke="#bbb" stroke-width="1.5"/></svg>
  <span>hello@kvrglobalinks.example</span>
</div>
<h5 class="abs foot-head" style="left:876px">SOCIAL MEDIA</h5>
<ul class="abs social" style="left:881px;top:3358px">
  <li><span class="dot"></span>Community</li>
  <li><span class="dot"></span>Updates</li>
  <li><span class="dot"></span>Network</li>
  <li><span class="dot"></span>Gallery</li>
</ul>
<p class="abs copy">© 2020 KVR Globalinks &nbsp;All right reserved</p>

</body>
</html>
```